Steady Ledger: Growing Practices Through Trust

Design a cover for this book which is designed to help a business go from it's current revenue and treatment acceptance to double (2X) that success and those metrics.

```html
<!DOCTYPE html>
<html lang="en">
<head>
<meta charset="utf-8">
<title>Steady Ledger: Growing Practices Through Trust — Book Cover</title>
<link rel="stylesheet" href="https://fonts.googleapis.com/css2?family=Anton&family=Open+Sans:wght@300;700&display=swap">
<style>
  :root {
    --backdrop: #232c40;
    --cover: #efece2;
    --ink-navy: #1f2a3c;
    --teal: #237a80;
    --orange: #e8792f;
    --leaf-green: #9cc06a;
    --mint: #7cc5b4;
    --author: #c9c3b4;
  }
  * { margin: 0; padding: 0; box-sizing: border-box; }
  html, body {
    width: 1200px;
    height: 864px;
    overflow: hidden;
    background: var(--backdrop);
  }
  .stage {
    width: 1200px;
    height: 864px;
    display: flex;
    align-items: center;
    justify-content: center;
  }
  .book-cover {
    position: relative;
    width: 560px;
    height: 800px;
    background: var(--cover);
    box-shadow: 0 18px 40px rgba(0, 0, 0, 0.35);
    overflow: hidden;
  }
  .cover-illustration {
    position: absolute;
    left: 40px;
    top: 36px;
    width: 480px;
    height: 480px;
  }
  .cover-title {
    position: absolute;
    left: 0;
    right: 0;
    top: 536px;
    text-align: center;
  }
  .title-kicker {
    display: block;
    font-family: "Open Sans", sans-serif;
    font-weight: 700;
    font-size: 38px;
    letter-spacing: 2px;
    color: var(--ink-navy);
    line-height: 1;
    padding-left: 50px;
  }
  .title-main {
    display: block;
    margin-top: 8px;
    font-family: "Anton", sans-serif;
    font-size: 56px;
    line-height: 1.05;
    color: var(--teal);
    letter-spacing: 1px;
  }
  .cover-authors {
    position: absolute;
    left: 0;
    right: 0;
    top: 742px;
    text-align: center;
    font-family: "Open Sans", sans-serif;
    font-weight: 300;
    font-size: 20px;
    letter-spacing: 7px;
    color: var(--author);
    text-transform: uppercase;
  }
</style>
</head>
<body>
  <main class="stage">
    <article class="book-cover">
      <svg class="cover-illustration" viewBox="0 0 480 480" role="img" aria-label="Illustration of a stylised teal tree whose branches carry orange, green and navy growth icons, charts and checkmarks, with lines hanging down like roots of data">
        <defs>
          <radialGradient id="canopy-glow" cx="50%" cy="45%" r="55%">
            <stop offset="0%" stop-color="var(--mint)" stop-opacity="0.55"/>
            <stop offset="45%" stop-color="var(--leaf-green)" stop-opacity="0.35"/>
            <stop offset="75%" stop-color="var(--orange)" stop-opacity="0.18"/>
            <stop offset="100%" stop-color="var(--cover)" stop-opacity="0"/>
          </radialGradient>
        </defs>
        <rect width="480" height="480" fill="url(#canopy-glow)"/>
      </svg>

      <h1 class="cover-title">
        <span class="title-kicker">STEADY LEDGER:</span>
        <span class="title-main">GROWING PRACTICES<br>THROUGH TRUST</span>
      </h1>

      <p class="cover-authors">Owen Harlow &amp; Dean Ashby</p>
    </article>
  </main>
</body>
</html>
```